Brightwell Forge, LLC
Electrical Contracting Company
We really like the back of #125 & #126 and the logo design on the front of #125.
We liked the front layout of #122, and we especially liked how they included the phrase Electrical Contracting Company on the card.
#118 we really like the front and back of your card. We like the colors, we like the shadowing.
We like the symbols for phone, cell, etc.
The above info was updated in the brief summary.
Please not changes to information:
instead of Electrical Contracting Corporation it needs to be Electrical Contracting Company
And the Fax number is 631-472-9083

```html
<!DOCTYPE html>
<html lang="en">
<head>
<meta charset="utf-8">
<title>Brightwell Forge, LLC — Business Card</title>
<link href="https://fonts.googleapis.com/css2?family=Roboto+Condensed:wght@400;700&family=Open+Sans:wght@400;600&display=swap" rel="stylesheet">
<style>
  :root {
    --bg: #3a3a3c;
    --card-white: #f7f7f5;
    --brand-yellow: #f2c21b;
    --ink: #1b1b1b;
    --ink-soft: #4a4a4a;
  }
  * { margin: 0; padding: 0; box-sizing: border-box; }
  html, body { width: 1200px; height: 799px; overflow: hidden; }
  body { background: var(--bg); position: relative; font-family: "Open Sans", sans-serif; }

  .card {
    position: absolute;
    width: 520px;
    height: 300px;
    border-radius: 18px;
    overflow: hidden;
    box-shadow: 0 10px 24px rgba(0,0,0,.45);
  }
  .card--front { left: 60px; top: 250px; background: var(--card-white); }
  .card--back  { left: 620px; top: 250px; background: var(--brand-yellow); }

  .contact-name {
    position: absolute; left: 300px; top: 24px;
    font-family: "Roboto Condensed", sans-serif; font-weight: 700;
    font-size: 30px; color: var(--ink); line-height: 1;
  }
  .contact-title {
    position: absolute; left: 302px; top: 58px;
    font-family: "Roboto Condensed", sans-serif; font-size: 14px; color: var(--ink-soft);
  }
  .contact-list {
    position: absolute; right: 22px; top: 94px;
    list-style: none; text-align: right;
    font-size: 12px; color: var(--ink-soft); line-height: 18px;
  }
  .contact-list li { display: flex; justify-content: flex-end; align-items: center; gap: 8px; }
  .contact-list li.address { margin-bottom: 8px; line-height: 16px; align-items: flex-start; }
  .contact-list svg { width: 13px; height: 13px; fill: var(--ink); flex: none; }

  .brand-block {
    position: absolute; left: 24px; top: 118px;
    width: 118px; height: 128px;
    background: var(--brand-yellow);
    display: flex; align-items: center; justify-content: center;
    text-align: center; padding: 10px;
  }
  .brand-name {
    font-family: "Roboto Condensed", sans-serif; font-weight: 700;
    font-size: 17px; line-height: 1.15; color: var(--ink);
  }

  .tagline-band {
    position: absolute; left: 0; right: 0; top: 256px; height: 22px;
    background: var(--brand-yellow);
    font-family: "Roboto Condensed", sans-serif; font-weight: 700;
    font-size: 12px; letter-spacing: .5px; color: var(--ink);
    padding-left: 24px; line-height: 22px; text-transform: uppercase;
  }

  .web-address {
    position: absolute; right: 26px; bottom: 26px;
    font-size: 12px; color: var(--ink);
  }
</style>
</head>
<body>

  <section class="card card--front">
    <h1 class="contact-name">Dana Whitlock</h1>
    <p class="contact-title">President</p>

    <ul class="contact-list">
      <li class="address">
        <span>48 Ridge Hollow Rd. Millbrook<br>NY 12545</span>
        <svg viewBox="0 0 16 16"><path d="M8 1 1 7.5h2V15h4v-4h2v4h4V7.5h2z"/></svg>
      </li>
      <li><span>6314725510</span>
        <svg viewBox="0 0 16 16"><path d="M3 2h3l1.5 3.5-2 1.3a8 8 0 0 0 3.7 3.7l1.3-2L14 10v3a1 1 0 0 1-1 1A12 12 0 0 1 2 3a1 1 0 0 1 1-1z"/></svg></li>
      <li><span>631558204</span>
        <svg viewBox="0 0 16 16"><path d="M5 1h6a1 1 0 0 1 1 1v12a1 1 0 0 1-1 1H5a1 1 0 0 1-1-1V2a1 1 0 0 1 1-1zm0 2v9h6V3zm3 10a.8.8 0 1 0 0 .1z"/></svg></li>
      <li><span>631-472-9083</span>
        <svg viewBox="0 0 16 16"><path d="M4 1h6l2 2v3h1a2 2 0 0 1 2 2v5h-3v2H4v-2H1V8a2 2 0 0 1 2-2h1zm1 1v4h6V3.5L9.5 2zm0 8v4h6v-4z"/></svg></li>
      <li><span>dana@brightwellforge.com</span>
        <svg viewBox="0 0 16 16"><path d="M1 3h14v10H1zm1.5 1.3V12h11V4.3L8 8.5z"/></svg></li>
    </ul>

    <div class="brand-block">
      <span class="brand-name">Brightwell Forge, LLC</span>
    </div>

    <div class="tagline-band">Electrical Contracting Company</div>
  </section>

  <section class="card card--back">
    <p class="web-address">www.brightwellforge.com</p>
  </section>

</body>
</html>
```